Letterhead, stationery and email signature for construction business

I need the letterhead, stationery and email signature designs for a construction business. I want them to have a corporate feel to them.

I've attached the logo for reference.

```html
<!DOCTYPE html>
<html lang="en">
<head>
<meta charset="utf-8">
<title>Halden Build – Business Card</title>
<link rel="stylesheet" href="https://fonts.googleapis.com/css2?family=Raleway:wght@700;800&family=Roboto:wght@400&display=swap">
<style>
  :root {
    --page-bg: #d9d6d2;
    --card-bg: #f3f4f5;
    --card-edge: #b9bcbf;
    --navy: #2c3f86;
    --ink-dark: #1f2530;
    --ink: #444a52;
    --ink-soft: #5a6068;
  }
  * { box-sizing: border-box; margin: 0; padding: 0; }
  html, body {
    width: 1200px;
    height: 1090px;
    overflow: hidden;
    background: var(--page-bg);
  }
  .business-card {
    position: absolute;
    left: 60px;
    top: 246px;
    width: 1080px;
    height: 598px;
    background: var(--card-bg);
    border: 1.5px solid var(--card-edge);
  }
  .brand {
    position: absolute;
    left: 560px;
    top: 100px;
    display: flex;
    align-items: center;
    gap: 18px;
  }
  .brand-square {
    width: 74px;
    height: 74px;
    background: var(--ink-dark);
  }
  .brand-name {
    font-family: "Raleway", sans-serif;
    font-weight: 800;
    font-size: 52px;
    letter-spacing: 1px;
    color: var(--navy);
    line-height: 1;
  }
  .holder {
    position: absolute;
    left: 83px;
    top: 232px;
  }
  .holder-name {
    font-family: "Raleway", sans-serif;
    font-weight: 700;
    font-size: 37px;
    color: var(--navy);
    line-height: 1.1;
  }
  .holder-role {
    font-family: "Raleway", sans-serif;
    font-weight: 700;
    font-size: 24px;
    color: var(--ink);
    margin-top: 6px;
  }
  .address {
    position: absolute;
    left: 83px;
    top: 340px;
    font-family: "Roboto", sans-serif;
    font-size: 27px;
    line-height: 38px;
    color: var(--ink-soft);
  }
  .contacts {
    position: absolute;
    left: 83px;
    top: 456px;
    display: flex;
    font-family: "Roboto", sans-serif;
    font-size: 27px;
    color: var(--ink-soft);
  }
  .contact-column { display: flex; flex-direction: column; gap: 6px; }
  .contact-divider {
    width: 2px;
    background: var(--navy);
    margin: 6px 22px 6px 20px;
  }
  .contact-line { display: flex; align-items: center; gap: 10px; line-height: 34px; }
  .contact-icon { width: 26px; height: 26px; fill: var(--navy); flex: none; }
</style>
</head>
<body>
  <main class="business-card">
    <div class="brand">
      <div class="brand-square"></div>
      <div class="brand-name">HALDEN BUILD</div>
    </div>

    <div class="holder">
      <h1 class="holder-name">Daniel Marsh</h1>
      <p class="holder-role">President</p>
    </div>

    <p class="address">Ashford House, 14 Carlton<br>Rd, London SE4 1QP</p>

    <div class="contacts">
      <div class="contact-column">
        <div class="contact-line">
          <svg class="contact-icon" viewBox="0 0 24 24" aria-hidden="true"><path d="M6.6 10.8a15.1 15.1 0 0 0 6.6 6.6l2.2-2.2a1 1 0 0 1 1-.25 11.4 11.4 0 0 0 3.6.57 1 1 0 0 1 1 1V20a1 1 0 0 1-1 1A17 17 0 0 1 3 4a1 1 0 0 1 1-1h3.5a1 1 0 0 1 1 1c0 1.25.2 2.45.57 3.57a1 1 0 0 1-.25 1z"/></svg>
          <span>(555) 318-4400</span>
        </div>
        <div class="contact-line">
          <svg class="contact-icon" viewBox="0 0 24 24" aria-hidden="true"><path d="M6 2h12v5H6zM3 8h18a2 2 0 0 1 2 2v7h-4v5H5v-5H1v-7a2 2 0 0 1 2-2zm4 8v4h10v-4z"/></svg>
          <span>(555) 318-4402</span>
        </div>
      </div>
      <div class="contact-divider"></div>
      <div class="contact-column">
        <div class="contact-line">
          <svg class="contact-icon" viewBox="0 0 24 24" aria-hidden="true"><path d="M2 5h20v14H2zm2 2v.4l8 5.2 8-5.2V7zm0 2.8V17h16V9.8l-8 5.2z"/></svg>
          <span>info@haldenbuild.com</span>
        </div>
        <div class="contact-line">
          <svg class="contact-icon" viewBox="0 0 24 24" aria-hidden="true"><path d="M12 2a10 10 0 1 0 0 20 10 10 0 0 0 0-20zm6.9 6h-2.9a15.7 15.7 0 0 0-1.4-3.6A8 8 0 0 1 18.9 8zM12 4c.8 1.2 1.5 2.5 1.9 4h-3.8c.4-1.5 1.1-2.8 1.9-4zM4.3 14a8.2 8.2 0 0 1 0-4h3.4a16.5 16.5 0 0 0 0 4zm.8 2h2.9c.3 1.3.8 2.5 1.4 3.6A8 8 0 0 1 5.1 16zM8 8H5.1a8 8 0 0 1 4.3-3.6C8.8 5.5 8.3 6.7 8 8zm4 12c-.8-1.2-1.5-2.5-1.9-4h3.8c-.4 1.5-1.1 2.8-1.9 4zm2.3-6H9.7a14.7 14.7 0 0 1 0-4h4.6a14.7 14.7 0 0 1 0 4zm.3 5.6c.6-1.1 1.1-2.3 1.4-3.6h2.9a8 8 0 0 1-4.3 3.6zm1.7-5.6a16.5 16.5 0 0 0 0-4h3.4a8.2 8.2 0 0 1 0 4z"/></svg>
          <span>www.haldenbuild.com</span>
        </div>
      </div>
    </div>
  </main>
</body>
</html>
```